Consulting Company PowerPoint Template Design

We are looking for an updated PowerPoint template design or our 55 person energy consulting firm (K7) based in San Francisco (www.kseven-example.com). We would like two versions of the same PowerPoint template in a 16:9 and 4:3 format with our existing logo.

We have an existing color scheme and template and are seeking your help to polish/update the template design for wide format and create a flexible template that is easy to use with content from Excel and Word. Our current template, and a couple of examples that we like are attached.

Specific requests include:

• Dark background for slide title
• A narrow section header
• Maximizing white space for content
• A limited number of well designed Master template layouts to choose from
• A selection of title and section header slides that are not San Francisco specific with some variety to chose from ideally with a focus on energy or nature, graphics/visuals.

For examples of energy specific templates see:
https://www.brightslidehub.example/energy/powerpoint-templates/0.html

Requirements
Must have
• Must use our logo but open to other designs, fonts, and styles for the PowerPoint template.
• Please use our existing color scheme found in the attached Excel file.
• Also we would like the ability to easily copy and paste from our existing/original template to the new template. In other words we would like backward compatibility to apply the new template format to our old PowerPoints that use our existing template.

```html
<!DOCTYPE html>
<html lang="en">
<head>
<meta charset="utf-8">
<title>K7 Energy Advisory – Presentation Template Overview</title>
<link href="https://fonts.googleapis.com/css2?family=Montserrat:wght@600;700;800&family=Open+Sans:wght@400;600;700&display=swap" rel="stylesheet">
<style>
  :root{
    --sheet:#1b1b1b;
    --navy:#1a5c82;
    --navy-deep:#124563;
    --gold:#e2b553;
    --ink:#3a3a3a;
    --muted:#8a8a8a;
    --paper:#ffffff;
    --green:#8bc34a;
    --blue:#2f80c4;
    --slate:#3d4b5a;
    --orange:#f4a43c;
    --red:#e53841;
    --grey:#bcbcbc;
  }
  html,body{margin:0;padding:0;width:1200px;height:912px;overflow:hidden;background:var(--sheet);}
  .board{position:relative;width:1200px;height:912px;}
  .slide{position:absolute;width:288px;height:217px;background:var(--paper);overflow:hidden;}
  .slide svg{display:block;width:288px;height:217px;}
  svg text{font-family:"Open Sans",Arial,sans-serif;}
  .display{font-family:"Montserrat",Arial,sans-serif;}
  .slide-title{font-size:9.5px;font-weight:600;fill:var(--navy);}
  .footer-text{font-size:4px;fill:#fff;font-weight:600;}
  .page-no{font-size:4px;fill:var(--navy-deep);font-weight:700;}
  .body-copy{font-size:3.6px;fill:var(--muted);}
  .body-strong{font-size:4.6px;fill:var(--navy);font-weight:600;}
  .label-dark{font-size:4px;fill:var(--ink);font-weight:600;}
  .brand-gold{fill:var(--gold);font-weight:700;}
  .col-1{left:12px}.col-2{left:306px}.col-3{left:601px}.col-4{left:898px}
  .row-1{top:12px}.row-2{top:234px}.row-3{top:458px}.row-4{top:682px}
</style>
</head>
<body>
<svg width="0" height="0" style="position:absolute" aria-hidden="true">
  <defs>
    <symbol id="header-mark" viewBox="0 0 16 16">
      <circle cx="8" cy="8" r="7.5" fill="#1a5c82"/>
      <text x="8" y="10.2" text-anchor="middle" font-size="6" font-weight="700" fill="#fff" font-family="Open Sans, Arial, sans-serif">K7</text>
    </symbol>
    <symbol id="slide-footer" viewBox="0 0 288 10">
      <rect x="0" y="0" width="288" height="10" fill="#1a5c82"/>
      <text x="4" y="6.6" font-size="4" font-weight="600" fill="#fff" font-family="Open Sans, Arial, sans-serif">K7 Energy Advisory</text>
      <polygon points="266,0 288,0 288,10 272,10" fill="#e2b553"/>
      <text x="280" y="6.6" font-size="4" font-weight="700" fill="#124563" text-anchor="middle" font-family="Open Sans, Arial, sans-serif">1</text>
    </symbol>
    <linearGradient id="navy-wash" x1="0" y1="0" x2="1" y2="1">
      <stop offset="0" stop-color="#1f6a93"/><stop offset="1" stop-color="#134a6a"/>
    </linearGradient>
  </defs>
</svg>

<main class="board">

  <!-- Title slide -->
  <section class="slide col-1 row-1">
    <svg viewBox="0 0 288 217">
      <rect width="288" height="217" fill="url(#navy-wash)"/>
      <circle cx="144" cy="104" r="14" fill="none" stroke="#ffffff" stroke-opacity=".8" stroke-width="1.4"/>
      <text x="144" y="107.5" text-anchor="middle" font-size="10" font-weight="700" fill="#fff">K7</text>
      <text x="144" y="142" text-anchor="middle" font-size="11" class="brand-gold">K7 Energy Advisory</text>
    </svg>
  </section>

  <!-- Section: energy + environment -->
  <section class="slide col-2 row-1">
    <svg viewBox="0 0 288 217">
      <text x="6" y="16" class="slide-title">Our Section</text>
      <use href="#header-mark" x="268" y="5" width="16" height="16"/>
      <rect x="0" y="26" width="288" height="183" fill="url(#navy-wash)" role="img" aria-label="Photo of solar panels under a blue sky, tinted blue"/>
      <text x="26" y="86" class="display" font-size="45" font-weight="800" fill="var(--gold)">ENERGY +</text>
      <text x="26" y="124" class="display" font-size="33" font-weight="800" fill="#fff">ENVIRONMENT</text>
      <g font-size="3.7" fill="#fff" font-style="italic">
        <text x="27" y="140">Lorem ipsum dolor sit amet consectetur adipiscing elit sed do eiusmod tempor incididunt ut labore et dolore</text>
        <text x="27" y="148">magna aliqua ut enim ad minim veniam quis nostrud exercitation ullamco laboris nisi ut aliquip ex ea</text>
        <text x="27" y="156">commodo consequat duis aute irure dolor in reprehenderit in voluptate velit esse cillum dolore fugiat</text>
        <text x="27" y="164">nulla pariatur excepteur sint occaecat cupidatat non proident sunt in culpa qui officia deserunt mollit</text>
        <text x="27" y="172">anim id est laborum sed ut perspiciatis unde omnis iste natus error sit voluptatem accusantium</text>
        <text x="27" y="184">doloremque laudantium totam rem aperiam eaque ipsa quae ab illo inventore veritatis et quasi</text>
        <text x="27" y="192">architecto beatae vitae dicta sunt explicabo nemo enim ipsam</text>
      </g>
      <use href="#slide-footer" x="0" y="209" width="288" height="8"/>
    </svg>
  </section>

  <!-- Section: quote -->
  <section class="slide col-3 row-1">
    <svg viewBox="0 0 288 217">
      <text x="6" y="16" class="slide-title">Our Section</text>
      <use href="#header-mark" x="268" y="5" width="16" height="16"/>
      <rect x="0" y="26" width="288" height="116" fill="#d9dde1" role="img" aria-label="Photo of a person reviewing plans and notes at a desk"/>
      <rect x="0" y="26" width="113" height="116" fill="#1a5c82" opacity=".82"/>
      <g text-anchor="middle" fill="#fff" font-size="11">
        <text x="76" y="57">“Innovation</text>
        <text x="76" y="71">distinguishes</text>
        <text x="76" y="85">between a</text>
        <text x="76" y="99">leader and a</text>
        <text x="76" y="113">follower.”</text>
        <text x="76" y="124" font-size="6.5">Dana Whitfield</text>
      </g>
      <text x="10" y="155" class="body-strong">Lorem ipsum dolor sit Lorem ipsum</text>
      <g class="body-copy">
        <text x="10" y="165">Lorem ipsum dolor sit amet consectetur adipiscing elit sed do eiusmod tempor incididunt ut labore et dolore magna</text>
        <text x="10" y="173">aliqua ut enim ad minim veniam quis nostrud exercitation ullamco laboris nisi ut aliquip ex ea commodo conseq</text>
        <text x="10" y="181">duis aute irure dolor in reprehenderit in voluptate velit esse cillum dolore eu fugiat nulla pariatur excepteur</text>
        <text x="10" y="189">sint occaecat cupidatat non proident sunt in culpa qui officia deserunt mollit anim id est laborum sed ut</text>
        <text x="10" y="197">perspiciatis unde omnis iste natus error sit</text>
      </g>
      <use href="#slide-footer" x="0" y="209" width="288" height="8"/>
    </svg>
  </section>

  <!-- Project title -->
  <section class="slide col-4 row-1">
    <svg viewBox="0 0 288 217">
      <rect width="288" height="217" fill="#f3f4f5"/>
      <circle cx="144" cy="62" r="15" fill="#1a5c82"/>
      <text x="144" y="66" text-anchor="middle" font-size="10" font-weight="700" fill="#fff">K7</text>
      <text x="144" y="98" text-anchor="middle" font-size="11" class="brand-gold">K7 Energy Advisory</text>
      <rect x="0" y="115" width="288" height="102" fill="url(#navy-wash)"/>
      <text x="144" y="155" text-anchor="middle" class="display" font-size="12.5" font-weight="700"><tspan fill="var(--gold)">PROJECT</tspan><tspan fill="#fff"> TITLE HERE</tspan></text>
      <text x="144" y="168" text-anchor="middle" font-size="6.5" fill="#cfe0ea">Subtext here Subtext here</text>
    </svg>
  </section>

  <!-- Features donut -->
  <section class="slide col-1 row-2">
    <svg viewBox="0 0 288 217">
      <text x="6" y="16" class="slide-title">Our Features</text>
      <use href="#header-mark" x="268" y="5" width="16" height="16"/>
      <g transform="translate(118 109)" fill="none" stroke-width="11">
        <circle r="45" stroke="#1a5c82" stroke-dasharray="90.5 282.7" transform="rotate(-60)"/>
        <circle r="45" stroke="#d6b566" stroke-dasharray="65 282.7" transform="rotate(55)"/>
        <circle r="45" stroke="#3d4b5a" stroke-dasharray="28 282.7" transform="rotate(138)"/>
        <circle r="45" stroke="#f39c2b" stroke-dasharray="34 282.7" transform="rotate(174)"/>
        <circle r="45" stroke="#e53841" stroke-dasharray="22 282.7" transform="rotate(217)"/>
        <circle r="45" stroke="#a9a9a9" stroke-dasharray="42 282.7" transform="rotate(245)"/>
      </g>
      <text x="118" y="108" text-anchor="middle" font-size="8.5" fill="#9a9a9a">YOUR</text>
      <text x="118" y="117" text-anchor="middle" font-size="8.5" fill="#9a9a9a">KEYWORD</text>
      <g stroke="#999" stroke-width=".4" fill="none">
        <polyline points="50,46 72,46 86,74"/><polyline points="190,46 176,46 160,80"/>
        <polyline points="30,81 68,90"/><polyline points="40,123 66,123"/>
        <polyline points="60,154 86,145"/><polyline points="100,186 126,186 134,160"/>
      </g>
      <g font-size="8" fill="#333" font-weight="600">
        <text x="40" y="45">15%</text><text x="186" y="45">32%</text><text x="24" y="80">8%</text>
        <text x="28" y="121">12%</text><text x="48" y="152">10%</text><text x="78" y="184">23%</text>
      </g>
      <g font-size="3" fill="#888">
        <text x="34" y="50">Lorem Ipsum</text><text x="186" y="50">Lorem Ipsum</text><text x="18" y="85">Lorem Ipsum</text>
        <text x="24" y="126">Lorem Ipsum</text><text x="44" y="157">Lorem Ipsum</text><text x="74" y="189">Lorem Ipsum</text>
      </g>
      <g class="body-copy">
        <text x="198" y="67">Lorem Ipsum is simply dummy text of the</text>
        <text x="198" y="75">printing and typesetting industry. Lorem</text>
        <text x="198" y="83">Ipsum has been the industry's standard</text>
        <text x="198" y="91">dummy text ever since the 1500s, when an</text>
        <text x="198" y="99">unknown printer took a galley of type and</text>
        <text x="198" y="107">scrambled it to make a type specimen</text>
        <text x="198" y="115">book. It has survived not only five centuries,</text>
        <text x="198" y="123">but also the leap into electronic typeset-</text>
        <text x="198" y="131">ting, remaining essentially unchanged.</text>
        <text x="198" y="139">Lorem Ipsum is simply dummy text of the</text>
        <text x="198" y="147">printing and typesetting industry. Lorem</text>
        <text x="198" y="155">Ipsum has been the industry's standard</text>
        <text x="198" y="163">dummy text ever since the 1500s, when an</text>
        <text x="198" y="171">unknown printer took a galley of type and</text>
      </g>
      <use href="#slide-footer" x="0" y="209" width="288" height="8"/>
    </svg>
  </section>

  <!-- Section with olive overlay -->
  <section class="slide col-2 row-2">
    <svg viewBox="0 0 288 217">
      <text x="6" y="16" class="slide-title">Our Section</text>
      <use href="#header-mark" x="268" y="5" width="16" height="16"/>
      <rect x="0" y="26" width="288" height="110" fill="url(#navy-wash)" role="img" aria-label="Photo of rows of solar panels in blue tones"/>
      <rect x="12" y="26" width="90" height="110" fill="#9a9a6a" opacity=".9"/>
      <g fill="#fff" font-style="italic" text-anchor="middle">
        <text x="57" y="50" font-size="5.5">Lorem ipsum dolor sit</text>
        <text x="57" y="58" font-size="5.5">Lorem ipsum</text>
        <g font-size="3.8">
          <text x="57" y="69">Lorem ipsum dolor sit Lorem</text>
          <text x="57" y="77">ipsum dolor sit Lorem ipsum dolor</text>
          <text x="57" y="85">sit Lorem ipsum dolor sit Lorem</text>
          <text x="57" y="93">ipsum dolor sit Lorem ipsum dolor</text>
          <text x="57" y="101">sit Lorem ipsum dolor sit Lorem</text>
          <text x="57" y="109">ipsum dolor si</text>
        </g>
      </g>
      <text x="10" y="155" class="body-strong">Lorem ipsum dolor sit Lorem ipsum</text>
      <g class="body-copy">
        <text x="10" y="165">Lorem ipsum dolor sit amet consectetur adipiscing elit sed do eiusmod tempor incididunt ut labore et dolore magna</text>
        <text x="10" y="173">aliqua ut enim ad minim veniam quis nostrud exercitation ullamco laboris nisi ut aliquip ex ea commodo conseq</text>
        <text x="10" y="181">duis aute irure dolor in reprehenderit in voluptate velit esse cillum dolore eu fugiat nulla pariatur excepteur</text>
        <text x="10" y="189">sint occaecat cupidatat non proident sunt in culpa qui officia deserunt mollit anim id est laborum sed ut</text>
        <text x="10" y="197">perspiciatis unde omnis iste natus error sit</text>
      </g>
      <use href="#slide-footer" x="0" y="209" width="288" height="8"/>
    </svg>
  </section>

  <!-- Agenda timeline -->
  <section class="slide col-3 row-2">
    <svg viewBox="0 0 288 217">
      <text x="6" y="16" class="slide-title">Our Section</text>
      <use href="#header-mark" x="268" y="5" width="16" height="16"/>
      <rect x="0" y="26" width="108" height="183" fill="#23272b" role="img" aria-label="Dark photo of hands typing on a laptop"/>
      <line x1="117" y1="40" x2="117" y2="190" stroke="#ccc" stroke-width=".5"/>
      <g>
        <circle cx="117" cy="50" r="2.6" fill="#fff" stroke="#e2b553" stroke-width="1"/>
        <circle cx="117" cy="80" r="2.6" fill="#fff" stroke="#e2b553" stroke-width="1"/>
        <circle cx="117" cy="108" r="2.6" fill="#fff" stroke="#1a5c82" stroke-width="1"/>
        <circle cx="117" cy="137" r="2.6" fill="#fff" stroke="#e53841" stroke-width="1"/>
        <circle cx="117" cy="166" r="2.6" fill="#fff" stroke="#e53841" stroke-width="1"/>
      </g>
      <g class="label-dark">
        <text x="126" y="49">The Presentation agenda comes here</text>
        <text x="126" y="79">The Presentation agenda comes here</text>
        <text x="126" y="107">The Presentation agenda comes here</text>
        <text x="126" y="136">The Presentation agenda comes here</text>
        <text x="126" y="165">The Presentation agenda comes here</text>
      </g>
      <g font-size="3" fill="#aaa">
        <text x="126" y="55">Lorem Ipsum is simply dummy text of the printing and typesetting industry.</text>
        <text x="126" y="85">Lorem Ipsum is simply dummy text of the printing and typesetting industry.</text>
        <text x="126" y="113">Lorem Ipsum is simply dummy text of the printing and typesetting industry.</text>
        <text x="126" y="142">Lorem Ipsum is simply dummy text of the printing and typesetting industry.</text>
        <text x="126" y="171">Lorem Ipsum is simply dummy text of the printing and typesetting industry.</text>
      </g>
      <use href="#slide-footer" x="0" y="209" width="288" height="8"/>
    </svg>
  </section>

  <!-- Title text with images -->
  <section class="slide col-4 row-2">
    <svg viewBox="0 0 288 217">
      <rect width="288" height="217" fill="#f4f5f6"/>
      <text x="12" y="16" class="display" font-size="9" font-weight="700"><tspan fill="#333">TITLE</tspan><tspan fill="var(--navy)"> TEXT HERE</tspan></text>
      <text x="12" y="25" font-size="3.6" fill="#999">Subtext here Subtext here Subtext here</text>
      <use href="#header-mark" x="268" y="7" width="16" height="16"/>
      <text x="12" y="54" class="body-strong">Lorem ipsum dolor sit Lorem ipsum</text>
      <g class="body-copy">
        <text x="12" y="63">Lorem ipsum dolor sit Lorem ipsum dolor sit Lorem</text>
        <text x="12" y="71">ipsum dolor sit Lorem ipsum dolor sit Lorem ipsum</text>
        <text x="12" y="79">dolor sit Lorem ipsum dolor sit Lorem ipsum dolor</text>
        <text x="12" y="87">sit Lorem ipsum dolor sit Lorem ipsum dolor sit</text>
        <text x="12" y="95">Lorem ipsum dolor sit Lorem ipsum dolor sit Lorem</text>
        <text x="12" y="103">ipsum dolor sit Lorem ipsum dolor sit Lorem ipsum</text>
        <text x="12" y="111">dolor sit Lorem ipsum dolor sit Lorem ipsum dolor</text>
        <text x="12" y="119">sit Lorem ipsum dolor sit Lorem ipsum dolor sit</text>
        <text x="12" y="127">Lorem ipsum dolor sit Lorem ipsum dolor sit Lorem</text>
        <text x="12" y="135">ipsum dolor sit Lorem ipsum dolor sit Lorem ipsum</text>
        <text x="12" y="143">dolor sit Lorem ipsum dolor sit Lorem ipsum dolor</text>
        <text x="12" y="155">Lorem ipsum dolor sit Lorem ipsum dolor sit Lorem</text>
        <text x="12" y="163">ipsum dolor sit Lorem ipsum dolor sit Lorem ipsum</text>
        <text x="12" y="171">sit Lorem ipsum dolor sit Lorem ipsum dolor sit</text>
        <text x="12" y="179">Lorem ipsum dolor sit</text>
      </g>
      <defs><linearGradient id="sky-grass" x1="0" y1="0" x2="0" y2="1"><stop offset="0" stop-color="#6aa6d8"/><stop offset=".75" stop-color="#cfe3f2"/><stop offset="1" stop-color="#5c9a3a"/></linearGradient></defs>
      <rect x="162" y="37" width="110" height="65" fill="url(#sky-grass)" role="img" aria-label="Photo of a wind turbine over a green field"/>
      <rect x="162" y="114" width="110" height="66" fill="#3f7fb8" role="img" aria-label="Illustration of power pylons in blue and yellow"/>
      <use href="#slide-footer" x="0" y="209" width="288" height="8"/>
    </svg>
  </section>

  <!-- Tabular data -->
  <section class="slide col-1 row-3">
    <svg viewBox="0 0 288 217">
      <text x="6" y="16" class="slide-title">Our Tabular Data</text>
      <use href="#header-mark" x="268" y="5" width="16" height="16"/>
      <g class="body-copy">
        <text x="11" y="48">Lorem Ipsum is simply dummy text of the printing and typesetting industry. Lorem Ipsum has been the industry's standard</text>
        <text x="11" y="57">dummy text ever since the 1500s, when an unknown printer took a galley of type and scrambled it to make a type specimen</text>
        <text x="11" y="65">book. It has survived not only five centuries, but also the leap into electronic typesetting, remaining essentially unchanged.</text>
        <text x="11" y="74">Lorem Ipsum is simply dummy text of the printing and typesetting industry. Lorem Ipsum has been the industry's standard</text>
        <text x="11" y="82">dummy text ever since the 1500s, when an unknown printer took a galley of type and scrambled it to make a type specimen</text>
        <text x="11" y="91">book. It has survived not only five centuries, but also the leap into electronic typesetting.</text>
      </g>
      <rect x="12" y="100" width="264" height="10" fill="#d6a63e"/>
      <g font-size="3" fill="#fff" font-weight="600">
        <text x="17" y="106">No</text><text x="35" y="106">Heading Comes here</text>
        <text x="127" y="106">Column Heading Here</text><text x="180" y="106">Column Heading Here</text><text x="231" y="106">Column Heading Here</text>
      </g>
      <g stroke="#e3e3e3" stroke-width=".4">
        <line x1="12" y1="121" x2="276" y2="121"/><line x1="12" y1="132" x2="276" y2="132"/>
        <line x1="12" y1="143" x2="276" y2="143"/><line x1="12" y1="154" x2="276" y2="154"/>
        <line x1="12" y1="165" x2="276" y2="165"/><line x1="12" y1="176" x2="276" y2="176"/>
        <line x1="28" y1="110" x2="28" y2="176"/><line x1="118" y1="110" x2="118" y2="176"/>
        <line x1="172" y1="110" x2="172" y2="176"/><line x1="224" y1="110" x2="224" y2="176"/>
      </g>
      <g font-size="3" fill="#999">
        <text x="18" y="117">1</text><text x="34" y="117">Lorem ipsum is simply dummy text</text><text x="132" y="117">$54,565,568</text><text x="185" y="117">$54,565,568</text><text x="238" y="117">$54,565,568</text>
        <text x="18" y="128">2</text><text x="34" y="128">Lorem ipsum is simply dummy text</text><text x="132" y="128">$54,565,568</text><text x="185" y="128">$54,565,568</text><text x="238" y="128">$54,565,568</text>
        <text x="18" y="139">3</text><text x="34" y="139">Lorem ipsum is simply dummy text</text><text x="132" y="139">$54,565,568</text><text x="185" y="139">$54,565,568</text><text x="238" y="139">$54,565,568</text>
        <text x="18" y="150">4</text><text x="34" y="150">Lorem ipsum is simply dummy text</text><text x="132" y="150">$54,565,568</text><text x="185" y="150">$54,565,568</text><text x="238" y="150">$54,565,568</text>
        <text x="18" y="161">5</text><text x="34" y="161">Lorem ipsum is simply dummy text</text><text x="132" y="161">$54,565,568</text><text x="185" y="161">$54,565,568</text><text x="238" y="161">$54,565,568</text>
        <text x="18" y="172">6</text><text x="34" y="172">Lorem ipsum is simply dummy text</text><text x="132" y="172">$54,565,568</text><text x="185" y="172">$54,565,568</text><text x="238" y="172">$54,565,568</text>
      </g>
      <use href="#slide-footer" x="0" y="209" width="288" height="8"/>
    </svg>
  </section>

  <!-- Features with phone -->
  <section class="slide col-2 row-3">
    <svg viewBox="0 0 288 217">
      <text x="6" y="16" class="slide-title">Our Features</text>
      <use href="#header-mark" x="268" y="5" width="16" height="16"/>
      <rect x="113" y="54" width="63" height="132" rx="9" fill="#f2f2f2" stroke="#cfcfcf" stroke-width=".8"/>
      <rect x="119" y="68" width="51" height="97" fill="#2a6e96" role="img" aria-label="Screen showing a power pylon against a blue sky"/>
      <circle cx="144.5" cy="176" r="4" fill="none" stroke="#cfcfcf" stroke-width=".6"/>
      <g class="label-dark" font-size="3.6">
        <text x="16" y="78">Lorem Ipsum is simply dummy</text>
        <text x="16" y="117">Lorem Ipsum is simply dummy</text>
        <text x="16" y="156">Lorem Ipsum is simply dummy</text>
        <text x="206" y="78">Lorem Ipsum is simply dummy</text>
        <text x="206" y="117">Lorem Ipsum is simply dummy</text>
        <text x="206" y="156">Lorem Ipsum is simply dummy</text>
      </g>
      <g font-size="2.8" fill="#999">
        <text x="16" y="83">Lorem Ipsum is simply dummy text of the</text><text x="16" y="87">printing and typesetting industry.</text>
        <text x="16" y="122">Lorem Ipsum is simply dummy text of the</text><text x="16" y="126">printing and typesetting industry.</text>
        <text x="16" y="161">Lorem Ipsum is simply dummy text of the</text><text x="16" y="165">printing and typesetting industry.</text>
        <text x="206" y="83">Lorem Ipsum is simply dummy text of the</text><text x="206" y="87">printing and typesetting industry.</text>
        <text x="206" y="122">Lorem Ipsum is simply dummy text of the</text><text x="206" y="126">printing and typesetting industry.</text>
        <text x="206" y="161">Lorem Ipsum is simply dummy text of the</text><text x="206" y="165">printing and typesetting industry.</text>
      </g>
      <circle cx="96" cy="81" r="8" fill="#e53841"/><circle cx="96" cy="120" r="8" fill="#3d4b5a"/><circle cx="96" cy="159" r="8" fill="#6ab04c"/>
      <circle cx="192" cy="81" r="8" fill="#8a8a8a"/><circle cx="192" cy="120" r="8" fill="#f4a43c"/><circle cx="192" cy="159" r="8" fill="#2f80c4"/>
      <g fill="none" stroke="#fff" stroke-width=".8">
        <rect x="92" y="77" width="8" height="8" rx="1"/><path d="M93 124v-8M99 124v-8"/><rect x="92" y="155" width="8" height="8"/>
        <circle cx="192" cy="81" r="3.5"/><path d="M188 116l8 8M196 116l-8 8"/><rect x="188" y="156" width="8" height="6" rx="1"/>
      </g>
      <use href="#slide-footer" x="0" y="209" width="288" height="8"/>
    </svg>
  </section>

  <!-- Bar chart -->
  <section class="slide col-3 row-3">
    <svg viewBox="0 0 288 217">
      <text x="6" y="16" class="slide-title">Our Graphs Chart</text>
      <use href="#header-mark" x="268" y="5" width="16" height="16"/>
      <g font-size="5" fill="#666" text-anchor="end">
        <text x="22" y="56">120</text><text x="22" y="70">100</text><text x="22" y="84">80</text><text x="22" y="98">60</text>
        <text x="22" y="112">40</text><text x="22" y="126">20</text><text x="22" y="140">0</text>
      </g>
      <g stroke="#eee" stroke-width=".4">
        <line x1="30" y1="54" x2="276" y2="54"/><line x1="30" y1="68" x2="276" y2="68"/><line x1="30" y1="82" x2="276" y2="82"/>
        <line x1="30" y1="96" x2="276" y2="96"/><line x1="30" y1="110" x2="276" y2="110"/><line x1="30" y1="124" x2="276" y2="124"/>
      </g>
      <line x1="30" y1="138" x2="276" y2="138" stroke="#aaa" stroke-width=".5"/>
      <!-- 0.7 px per unit -->
      <g>
        <rect x="34" y="68" width="4.5" height="70" fill="var(--green)"/><rect x="39" y="75" width="4.5" height="63" fill="var(--red)"/>
        <rect x="54" y="75" width="4.5" height="63" fill="var(--blue)"/><rect x="59" y="82" width="4.5" height="56" fill="var(--blue)"/>
        <rect x="74" y="103" width="4.5" height="35" fill="var(--slate)"/><rect x="79" y="68" width="4.5" height="70" fill="var(--blue)"/><rect x="84" y="68" width="4.5" height="70" fill="var(--grey)"/>
        <rect x="94" y="96" width="4.5" height="42" fill="var(--orange)"/><rect x="99" y="68" width="4.5" height="70" fill="var(--red)"/>
        <rect x="114" y="68" width="4.5" height="70" fill="var(--red)"/><rect x="119" y="75" width="4.5" height="63" fill="var(--orange)"/>
        <rect x="134" y="96" width="4.5" height="42" fill="var(--orange)"/><rect x="139" y="89" width="4.5" height="49" fill="var(--grey)"/>
        <rect x="154" y="68" width="4.5" height="70" fill="var(--green)"/><rect x="159" y="103" width="4.5" height="35" fill="var(--blue)"/>
        <rect x="174" y="82" width="4.5" height="56" fill="var(--blue)"/><rect x="179" y="96" width="4.5" height="42" fill="var(--green)"/>
        <rect x="194" y="117" width="4.5" height="21" fill="var(--slate)"/><rect x="199" y="75" width="4.5" height="63" fill="var(--blue)"/>
        <rect x="214" y="89" width="4.5" height="49" fill="var(--orange)"/><rect x="219" y="82" width="4.5" height="56" fill="var(--orange)"/>
        <rect x="234" y="68" width="4.5" height="70" fill="var(--red)"/><rect x="239" y="68" width="4.5" height="70" fill="var(--red)"/>
        <rect x="254" y="103" width="4.5" height="35" fill="var(--grey)"/><rect x="259" y="68" width="4.5" height="70" fill="var(--grey)"/>
      </g>
      <g font-size="5" fill="#666" text-anchor="middle">
        <text x="39" y="149">Jan</text><text x="59" y="149">Feb</text><text x="79" y="149">Mar</text><text x="99" y="149">Apr</text>
        <text x="119" y="149">May</text><text x="139" y="149">Jun</text><text x="159" y="149">Jul</text><text x="179" y="149">Aug</text>
        <text x="199" y="149">Sep</text><text x="219" y="149">Act</text><text x="239" y="149">Nov</text><text x="259" y="149">Dec</text>
      </g>
      <g class="body-copy">
        <text x="16" y="170">Lorem ipsum dolor sit Lorem ipsum dolor sit Lorem ipsum dolor sit Lorem ipsum dolor sit Lorem ipsum dolor sit Lorem</text>
        <text x="16" y="178">ipsum dolor sit Lorem ipsum dolor sit Lorem ipsum dolor sit Lorem ipsum dolor sit Lorem ipsum dolor sit Lorem ipsum</text>
        <text x="16" y="186">dolor sit Lorem ipsum dolor sit Lorem ipsum dolor sit Lorem ipsum dolor sit</text>
      </g>
      <use href="#slide-footer" x="0" y="209" width="288" height="8"/>
    </svg>
  </section>

  <!-- Main activities -->
  <section class="slide col-4 row-3">
    <svg viewBox="0 0 288 217">
      <rect width="288" height="217" fill="#f6f7f8"/>
      <text x="6" y="16" class="slide-title">Our Section</text>
      <use href="#header-mark" x="268" y="5" width="16" height="16"/>
      <text x="14" y="44" class="body-strong">Our Main Activities</text>
      <g class="body-copy">
        <text x="14" y="53">Lorem ipsum dolor sit Lorem ipsum dolor sit Lorem ipsum dolor sit Lorem ipsum dolor sit Lorem ipsum dolor sit Lorem</text>
        <text x="14" y="61">dolor sit Lorem ipsum dolor sit Lorem ipsum dolor sit Lorem ipsum dolor sit Lorem ipsum dolor sit Lorem ipsum</text>
        <text x="14" y="69">Lorem ipsum dolor sit Lorem ipsum dolor sit Lorem ipsum dolor sit</text>
      </g>
      <g fill="#1a5c82">
        <circle cx="40" cy="98" r="13"/><circle cx="106" cy="98" r="13"/><circle cx="177" cy="98" r="13"/><circle cx="243" cy="98" r="13"/>
      </g>
      <g fill="none" stroke="#fff" stroke-width="1.2">
        <circle cx="40" cy="95" r="3"/><path d="M34 105q6-6 12 0"/>
        <rect x="101" y="93" width="10" height="8" rx="1"/>
        <circle cx="177" cy="98" r="5"/><circle cx="177" cy="98" r="1.6"/>
        <path d="M237 104h12M239 104v-6M243 104v-9M247 104v-4"/>
      </g>
      <g font-size="4" fill="#1a5c82" font-weight="600" text-anchor="middle">
        <text x="40" y="121">Our Main Activities</text><text x="106" y="121">Our Main Activities</text>
        <text x="177" y="121">Our Main Activities</text><text x="243" y="121">Our Main Activities</text>
      </g>
      <g class="body-copy">
        <text x="20" y="131">Lorem ipsum dolor sit</text><text x="20" y="139">Lorem ipsum dolor sit</text><text x="20" y="147">Lorem ipsum dolor sit</text>
        <text x="20" y="155">Lorem ipsum dolor sit</text><text x="20" y="163">Lorem ipsum dolor sit</text><text x="20" y="171">Lorem ipsum dolor sit</text>
        <text x="86" y="131">Lorem ipsum dolor sit</text><text x="86" y="139">Lorem ipsum dolor sit</text><text x="86" y="147">Lorem ipsum dolor sit</text>
        <text x="86" y="155">Lorem ipsum dolor sit</text><text x="86" y="163">Lorem ipsum dolor sit</text><text x="86" y="171">Lorem ipsum dolor sit</text>
        <text x="157" y="131">Lorem ipsum dolor sit</text><text x="157" y="139">Lorem ipsum dolor sit</text><text x="157" y="147">Lorem ipsum dolor sit</text>
        <text x="157" y="155">Lorem ipsum dolor sit</text><text x="157" y="163">Lorem ipsum dolor sit</text><text x="157" y="171">Lorem ipsum dolor sit</text>
        <text x="223" y="131">Lorem ipsum dolor sit</text><text x="223" y="139">Lorem ipsum dolor sit</text><text x="223" y="147">Lorem ipsum dolor sit</text>
        <text x="223" y="155">Lorem ipsum dolor sit</text><text x="223" y="163">Lorem ipsum dolor sit</text><text x="223" y="171">Lorem ipsum dolor sit</text>
      </g>
      <use href="#slide-footer" x="0" y="209" width="288" height="8"/>
    </svg>
  </section>

  <!-- Social media chart -->
  <section class="slide col-1 row-4">
    <svg viewBox="0 0 288 217">
      <text x="6" y="16" class="slide-title">Our Social Media Chart</text>
      <use href="#header-mark" x="268" y="5" width="16" height="16"/>
      <g font-size="3.3" font-weight="700" fill="#fff" text-anchor="middle">
        <circle cx="38" cy="68" r="11" fill="#3b5a99"/><text x="38" y="69.5">Friendo</text>
        <circle cx="107" cy="80" r="11" fill="#1da1e0"/><text x="107" y="81.5">Chirpa</text>
        <circle cx="176" cy="88" r="11" fill="#d73d32"/><text x="176" y="89.5">Plusly</text>
        <circle cx="244" cy="101" r="11" fill="#1b75b0"/><text x="244" y="102.5">Linkr</text>
      </g>
      <g>
        <rect x="32" y="98" width="9" height="42" fill="#3b5a99"/><rect x="42" y="86" width="9" height="54" fill="#5070b0"/><rect x="52" y="112" width="9" height="28" fill="#7890c2"/><rect x="62" y="104" width="9" height="36" fill="#a9b8d9"/>
        <rect x="100" y="92" width="9" height="48" fill="#1da1e0"/><rect x="110" y="122" width="9" height="18" fill="#46b4e8"/><rect x="120" y="110" width="9" height="30" fill="#77c8ee"/><rect x="130" y="116" width="9" height="24" fill="#aadcf4"/>
        <rect x="168" y="116" width="9" height="24" fill="#d73d32"/><rect x="178" y="106" width="9" height="34" fill="#de5c53"/><rect x="188" y="98" width="9" height="42" fill="#e7857e"/><rect x="198" y="92" width="9" height="48" fill="#efaaa5"/>
        <rect x="236" y="116" width="9" height="24" fill="#1b75b0"/><rect x="246" y="122" width="9" height="18" fill="#4a92c2"/><rect x="256" y="116" width="9" height="24" fill="#7cb0d4"/><rect x="266" y="118" width="9" height="22" fill="#b0d0e6"/>
      </g>
      <g stroke="#ddd" stroke-width=".4"><line x1="22" y1="140" x2="80" y2="140"/><line x1="90" y1="140" x2="148" y2="140"/><line x1="158" y1="140" x2="216" y2="140"/><line x1="226" y1="140" x2="282" y2="140"/></g>
      <g font-size="3" fill="#888" text-anchor="middle"><text x="51" y="146">5/10/15</text><text x="119" y="146">5/10/15</text><text x="187" y="146">5/10/15</text><text x="255" y="146">5/10/15</text></g>
      <g class="body-copy">
        <text x="10" y="160">Lorem ipsum dolor sit Lorem ipsum dolor sit Lorem ipsum dolor sit Lorem ipsum dolor sit Lorem ipsum dolor sit Lorem</text>
        <text x="10" y="168">ipsum dolor sit Lorem ipsum dolor sit Lorem ipsum dolor sit Lorem ipsum dolor sit Lorem ipsum dolor sit Lorem ipsum</text>
        <text x="10" y="176">dolor sit Lorem ipsum dolor sit Lorem ipsum dolor sit Lorem ipsum dolor sit</text>
      </g>
      <use href="#slide-footer" x="0" y="209" width="288" height="8"/>
    </svg>
  </section>

  <!-- Timeline organise chart -->
  <section class="slide col-2 row-4">
    <svg viewBox="0 0 288 217">
      <text x="6" y="16" class="slide-title">Our Organise Chart</text>
      <use href="#header-mark" x="268" y="5" width="16" height="16"/>
      <g class="body-copy">
        <text x="16" y="41">Lorem ipsum dolor sit Lorem ipsum dolor sit Lorem ipsum dolor sit Lorem ipsum dolor sit Lorem ipsum dolor sit Lorem</text>
        <text x="16" y="49">ipsum dolor sit Lorem ipsum dolor sit Lorem ipsum dolor sit Lorem ipsum dolor sit Lorem ipsum dolor sit Lorem ipsum</text>
        <text x="16" y="57">dolor sit Lorem ipsum dolor sit Lorem ipsum dolor sit</text>
      </g>
      <g fill="#fff" stroke-width=".8">
        <circle cx="30" cy="94" r="13" stroke="#8bc34a"/><circle cx="120" cy="94" r="13" stroke="#3d4b5a"/><circle cx="210" cy="94" r="13" stroke="#e53841"/>
        <circle cx="75" cy="175" r="13" stroke="#2f80c4"/><circle cx="165" cy="175" r="13" stroke="#f4a43c"/><circle cx="255" cy="175" r="13" stroke="#9a9a9a"/>
      </g>
      <g fill="none" stroke-width="1">
        <rect x="25" y="90" width="10" height="8" stroke="#8bc34a"/><ellipse cx="120" cy="94" rx="5" ry="6" stroke="#3d4b5a"/>
        <circle cx="210" cy="94" r="4" stroke="#e53841"/><path d="M70 180l10-10" stroke="#2f80c4"/>
        <rect x="159" y="171" width="12" height="8" rx="1" stroke="#f4a43c"/><circle cx="255" cy="173" r="4" stroke="#9a9a9a"/>
      </g>
      <g font-size="3.2" fill="#777">
        <text x="48" y="88">Lorem Ipsum is</text><text x="48" y="94">simply dummy text of</text><text x="48" y="100">the printing and</text><text x="48" y="106">typesetting industry.</text>
        <text x="138" y="88">Lorem Ipsum is</text><text x="138" y="94">simply dummy text of</text><text x="138" y="100">the printing and</text><text x="138" y="106">typesetting industry.</text>
        <text x="228" y="88">Lorem Ipsum is</text><text x="228" y="94">simply dummy text of</text><text x="228" y="100">the printing and</text><text x="228" y="106">typesetting industry.</text>
        <text x="12" y="166">Lorem Ipsum is</text><text x="12" y="172">simply dummy text of</text><text x="12" y="178">the printing and</text><text x="12" y="184">typesetting industry</text>
        <text x="102" y="166">Lorem Ipsum is</text><text x="102" y="172">simply dummy text of</text><text x="102" y="178">the printing and</text><text x="102" y="184">typesetting industry</text>
        <text x="192" y="166">Lorem Ipsum is</text><text x="192" y="172">simply dummy text of</text><text x="192" y="178">the printing and</text><text x="192" y="184">typesetting industry</text>
      </g>
      <g>
        <polygon points="6,129 52,129 56,134 52,139 6,139" fill="#8bc34a"/>
        <polygon points="52,129 98,129 102,134 98,139 52,139 56,134" fill="#2f80c4"/>
        <polygon points="98,129 144,129 148,134 144,139 98,139 102,134" fill="#3d4b5a"/>
        <polygon points="144,129 190,129 194,134 190,139 144,139 148,134" fill="#f4a43c"/>
        <polygon points="190,129 236,129 240,134 236,139 190,139 194,134" fill="#e53841"/>
        <polygon points="236,129 282,129 286,134 282,139 236,139 240,134" fill="#a5a5a5"/>
      </g>
      <g font-size="5" fill="#fff" font-weight="600" text-anchor="middle">
        <text x="30" y="136">1986</text><text x="77" y="136">1990</text><text x="123" y="136">2000</text>
        <text x="169" y="136">2005</text><text x="215" y="136">2011</text><text x="261" y="136">2015</text>
      </g>
      <use href="#slide-footer" x="0" y="209" width="288" height="8"/>
    </svg>
  </section>

  <!-- Box organise chart -->
  <section class="slide col-3 row-4">
    <svg viewBox="0 0 288 217">
      <text x="6" y="16" class="slide-title">Our Organise Chart</text>
      <use href="#header-mark" x="268" y="5" width="16" height="16"/>
      <g fill="none" stroke="#d8d8d8" stroke-width=".5">
        <path d="M118 94H84M118 94v-36M118 94v36M118 58H84M118 82H84M118 130H84M118 106v0M84 58"/>
        <path d="M118 58v0"/>
        <path d="M170 94h34M170 94v-36M170 94v36M170 58h34M170 82h34M170 130h34"/>
        <path d="M118 94v48M170 94v48M84 142h34M170 142h34M84 118h34M170 118h34"/>
        <path d="M40 53h14v5h14M40 66h14v-8M40 84h14M40 97h14v-15M40 115h14M40 128h14v-13M40 143h14M40 156h14v-13M40 171h14M40 184h14v-13"/>
        <path d="M248 53h-14v5h-14M248 66h-14v-8M248 84h-14M248 97h-14v-15M248 115h-14M248 128h-14v-13M248 143h-14M248 156h-14v-13M248 171h-14M248 184h-14v-13"/>
      </g>
      <rect x="118" y="74" width="52" height="40" fill="#fff" stroke="#1a5c82" stroke-width="1"/>
      <circle cx="144" cy="94" r="8" fill="none" stroke="#333" stroke-width=".8"/>
      <circle cx="144" cy="91.5" r="2.6" fill="none" stroke="#333" stroke-width=".7"/>
      <path d="M139 99q5-5 10 0" fill="none" stroke="#333" stroke-width=".7"/>
      <g fill="#fff" stroke="#e2b553" stroke-width=".6">
        <rect x="54" y="52" width="30" height="12"/><rect x="54" y="82" width="30" height="12"/><rect x="54" y="112" width="30" height="12"/>
        <rect x="54" y="139" width="30" height="12"/><rect x="54" y="166" width="30" height="12"/>
        <rect x="204" y="52" width="30" height="12"/><rect x="204" y="82" width="30" height="12"/><rect x="204" y="112" width="30" height="12"/>
        <rect x="204" y="139" width="30" height="12"/><rect x="204" y="166" width="30" height="12"/>
      </g>
      <g fill="#fff" stroke="#e53841" stroke-width=".6">
        <rect x="6" y="49" width="34" height="7"/><rect x="6" y="62" width="34" height="7"/><rect x="6" y="80" width="34" height="7"/><rect x="6" y="93" width="34" height="7"/>
        <rect x="6" y="111" width="34" height="7"/><rect x="6" y="124" width="34" height="7"/><rect x="6" y="139" width="34" height="7"/><rect x="6" y="152" width="34" height="7"/>
        <rect x="6" y="167" width="34" height="7"/><rect x="6" y="180" width="34" height="7"/>
        <rect x="248" y="49" width="34" height="7"/><rect x="248" y="62" width="34" height="7"/><rect x="248" y="80" width="34" height="7"/><rect x="248" y="93" width="34" height="7"/>
        <rect x="248" y="111" width="34" height="7"/><rect x="248" y="124" width="34" height="7"/><rect x="248" y="139" width="34" height="7"/><rect x="248" y="152" width="34" height="7"/>
        <rect x="248" y="167" width="34" height="7"/><rect x="248" y="180" width="34" height="7"/>
      </g>
      <g font-size="3" fill="#333" font-weight="600">
        <text x="20" y="54">CHILD 1</text><text x="20" y="67">CHILD 2</text><text x="20" y="85">CHILD 1</text><text x="20" y="98">CHILD 2</text>
        <text x="20" y="116">CHILD 1</text><text x="20" y="129">CHILD 2</text><text x="20" y="144">CHILD 1</text><text x="20" y="157">CHILD 2</text>
        <text x="20" y="172">CHILD 1</text><text x="20" y="185">CHILD 2</text>
        <text x="262" y="54">CHILD 1</text><text x="262" y="67">CHILD 2</text><text x="262" y="85">CHILD 1</text><text x="262" y="98">CHILD 2</text>
        <text x="262" y="116">CHILD 1</text><text x="262" y="129">CHILD 2</text><text x="262" y="144">CHILD 1</text><text x="262" y="157">CHILD 2</text>
        <text x="262" y="172">CHILD 1</text><text x="262" y="185">CHILD 2</text>
      </g>
      <g font-size="3" fill="#333" text-anchor="middle">
        <text x="69" y="58" font-weight="700">HEAD 2</text><text x="69" y="62">Department Name</text>
        <text x="69" y="88" font-weight="700">HEAD 3</text><text x="69" y="92">Department Name</text>
        <text x="69" y="118" font-weight="700">HEAD 4</text><text x="69" y="122">Department Name</text>
        <text x="69" y="145" font-weight="700">HEAD 5</text><text x="69" y="149">Department Name</text>
        <text x="69" y="172" font-weight="700">HEAD 5</text><text x="69" y="176">Department Name</text>
        <text x="219" y="58" font-weight="700">HEAD 6</text><text x="219" y="62">Department Name</text>
        <text x="219" y="88" font-weight="700">HEAD 7</text><text x="219" y="92">Department Name</text>
        <text x="219" y="118" font-weight="700">HEAD 8</text><text x="219" y="122">Department Name</text>
        <text x="219" y="145" font-weight="700">HEAD 9</text><text x="219" y="149">Department Name</text>
        <text x="219" y="172" font-weight="700">HEAD 9</text><text x="219" y="176">Department Name</text>
      </g>
      <use href="#slide-footer" x="0" y="209" width="288" height="8"/>
    </svg>
  </section>

  <!-- Closing slide -->
  <section class="slide col-4 row-4">
    <svg viewBox="0 0 288 217">
      <rect width="288" height="217" fill="#f4f5f6"/>
      <rect x="0" y="0" width="288" height="140" fill="url(#navy-wash)" role="img" aria-label="Photo of a handshake, tinted blue"/>
      <text x="144" y="86" text-anchor="middle" class="display" font-size="14" font-weight="700" fill="#fff">THANKS FOR YOUR TIME</text>
      <circle cx="90" cy="166" r="10" fill="#1a5c82"/>
      <text x="90" y="169" text-anchor="middle" font-size="7" font-weight="700" fill="#fff">K7</text>
      <text x="90" y="188" text-anchor="middle" font-size="8" class="brand-gold">K7 Energy Advisory</text>
      <g fill="#1a5c82">
        <circle cx="187" cy="158" r="4"/><circle cx="187" cy="176" r="4"/><circle cx="187" cy="194" r="4"/>
      </g>
      <g fill="none" stroke="#fff" stroke-width=".7">
        <path d="M185.5 156.3q0 3.4 3 3.4"/><rect x="185" y="174.7" width="4" height="2.6"/><circle cx="187" cy="194" r="1.8"/>
      </g>
      <g font-size="5.5" fill="#333">
        <text x="195" y="160">+1 415 555 0142</text>
        <text x="195" y="178">hello@kseven-example.com</text>
        <text x="195" y="196">www.kseven-example.com</text>
      </g>
      <polygon points="272,208 288,208 288,217 276,217" fill="#e2b553"/>
    </svg>
  </section>

</main>
</body>
</html>
```